Business card for Luxury Portable Restroom Trailer company

We are a Luxury Portable Restroom Trailer Company Called FALCRIDGE HIRES. Based in Orange County California. We provide portable restroom trailers for events, such as, Weddings, Concerts, Charity events, Sporting events, Tournaments, Corporate events, ect. We rent and Sell the Luxury restrooms. Our colors are white, grey, and Orange. As you will see in the logo we uploaded.
There are 2 people in the company so the names and titles will change for the 3 people but card will remain the same. Here is the information for each Person: Dwight Penner CFO 555 318-0476
next Person: Leon Marchetti VP 555 318-0476
Next Person: Owen Marchetti CEO 555 318-0476
Information to include on the card: Luxury Restroom Trailers Rental and Sales. Weddings, Concerts, Charity, Sporting and Corp. Events.

```html
<!DOCTYPE html>
<html lang="en">
<head>
<meta charset="utf-8">
<title>FALCRIDGE HIRES – Business Card</title>
<link rel="stylesheet" href="https://fonts.googleapis.com/css2?family=Montserrat:wght@400;700;800&display=swap">
<style>
  :root {
    --backdrop: #2b2b2b;
    --card: #181818;
    --orange: #f36f24;
    --white: #ffffff;
    --emboss: #272727;
  }
  * { box-sizing: border-box; margin: 0; padding: 0; }
  html, body {
    width: 1200px; height: 853px; overflow: hidden;
    background: var(--backdrop);
    font-family: "Montserrat", sans-serif;
  }
  .canvas {
    position: relative; width: 1200px; height: 853px;
    display: flex; align-items: center; justify-content: center; gap: 40px;
  }
  .card {
    position: relative; width: 540px; height: 309px;
    background: var(--card); overflow: hidden;
  }
  /* Front */
  .card-front .brand-name {
    position: absolute; left: 30px; top: 30px;
    color: var(--orange); font-weight: 800; font-size: 19px; letter-spacing: 1px;
  }
  .brand-art {
    position: absolute; left: 262px; top: 0; width: 278px; height: 309px;
    background: var(--orange);
  }
  .team { position: absolute; left: 36px; top: 78px; }
  .member { margin-bottom: 12px; line-height: 1.2; }
  .member-name { color: var(--orange); font-weight: 700; font-size: 17px; }
  .member-title { color: var(--white); font-size: 12px; margin-left: 14px; }
  .member-phone {
    color: var(--white); font-size: 12px; margin-left: 14px;
    display: flex; align-items: center; gap: 6px;
  }
  .member-phone svg { width: 11px; height: 11px; fill: var(--orange); }
  /* Back */
  .card-back .brand-name {
    position: absolute; left: 0; right: 0; top: 92px; text-align: center;
    color: var(--emboss); font-weight: 800; font-size: 44px; letter-spacing: 2px;
  }
  .tagline {
    position: absolute; left: 0; right: 0; top: 214px; text-align: center;
    color: var(--white); font-size: 13px; line-height: 1.5;
  }
</style>
</head>
<body>
<main class="canvas">
  <section class="card card-front">
    <div class="brand-name">FALCRIDGE HIRES</div>
    <div class="brand-art" role="img" aria-label="Large orange brand artwork panel"></div>
    <div class="team">
      <div class="member">
        <div class="member-name">Dwight Penner</div>
        <div class="member-title">CFO</div>
        <div class="member-phone"><svg viewBox="0 0 24 24"><path d="M6.6 10.8a15 15 0 0 0 6.6 6.6l2.2-2.2a1 1 0 0 1 1-.25 11.4 11.4 0 0 0 3.6.57 1 1 0 0 1 1 1V20a1 1 0 0 1-1 1A17 17 0 0 1 3 4a1 1 0 0 1 1-1h3.5a1 1 0 0 1 1 1c0 1.25.2 2.45.57 3.6a1 1 0 0 1-.25 1z"/></svg>555 318-0476</div>
      </div>
      <div class="member">
        <div class="member-name">Leon Marchetti</div>
        <div class="member-title">VP</div>
        <div class="member-phone"><svg viewBox="0 0 24 24"><path d="M6.6 10.8a15 15 0 0 0 6.6 6.6l2.2-2.2a1 1 0 0 1 1-.25 11.4 11.4 0 0 0 3.6.57 1 1 0 0 1 1 1V20a1 1 0 0 1-1 1A17 17 0 0 1 3 4a1 1 0 0 1 1-1h3.5a1 1 0 0 1 1 1c0 1.25.2 2.45.57 3.6a1 1 0 0 1-.25 1z"/></svg>555 318-0476</div>
      </div>
      <div class="member">
        <div class="member-name">Owen Marchetti</div>
        <div class="member-title">CEO</div>
        <div class="member-phone"><svg viewBox="0 0 24 24"><path d="M6.6 10.8a15 15 0 0 0 6.6 6.6l2.2-2.2a1 1 0 0 1 1-.25 11.4 11.4 0 0 0 3.6.57 1 1 0 0 1 1 1V20a1 1 0 0 1-1 1A17 17 0 0 1 3 4a1 1 0 0 1 1-1h3.5a1 1 0 0 1 1 1c0 1.25.2 2.45.57 3.6a1 1 0 0 1-.25 1z"/></svg>555 318-0476</div>
      </div>
    </div>
  </section>

  <section class="card card-back">
    <div class="brand-name">FALCRIDGE HIRES</div>
    <p class="tagline">Luxury Restroom Trailers Rental and Sales.<br>Weddings, Concerts, Charity, Sporting and Corp. Events.</p>
  </section>
</main>
</body>
</html>
```